Fresh, modern, fun business card for pediatric dental practice

Need a business card for fresh, modern, fun pediatric dental practice

Clean look that matches our website's font and colors

We prefer the look of curved corners on business cards

Target Market(s)

parents (mothers) of young children, professionals, mid-high class

Industry/Entity Type

Dental

Contact Information for Business Card

Maplebrook Pediatric Dentistry
482 Quarry Lane
Suite 517
Fairhollow, PA 17599
717.555.0193
www.maplebrookkidsdental.example

Mei-Ran Tsai, DMD
Corinne Walbeck, DMD
(we are working on our email address, but we would like that on the card as well)

Font styles to use
Sans Serif

Requirements
Must have
• All info; we would also like to make cards for individual staff members
• colors from our website and color palatte, attatched
• use same font and design as website for branding
Nice to have
• clean, simple card that has a pop of color
• we would like to see a few designs with our tag line "where smiles get brighter"
• we are not sure if we want to have it on there or not
• we would like to see a few designs incorporating the ribbon graphic on our website where the word WELCOME is

```html
<!DOCTYPE html>
<html lang="en">
<head>
<meta charset="utf-8">
<title>Maplebrook Pediatric Dentistry – Business Card</title>
<link rel="stylesheet" href="https://fonts.googleapis.com/css2?family=Open+Sans:wght@600&family=Raleway:wght@500&family=Lato:wght@400&display=swap">
<style>
  :root {
    --stage: #1e1e1e;
    --card-white: #ffffff;
    --sun-orange: #f5a81c;
    --band-yellow: #f8b827;
    --magenta: #d63a8c;
    --ink: #333333;
    --white: #ffffff;
  }
  * { margin: 0; padding: 0; box-sizing: border-box; }
  html, body {
    width: 1200px; height: 900px; overflow: hidden;
    background: var(--stage);
  }
  .canvas { position: relative; width: 1200px; height: 900px; }
  .card {
    position: absolute; top: 306px;
    width: 439px; height: 271px;
    border-radius: 12px; overflow: hidden;
    box-shadow: 3px 4px 8px rgba(0,0,0,.45);
  }
  /* Contact side */
  .card--contact { left: 149px; background: var(--card-white); }
  .practice-name {
    position: absolute;
    font-family: "Open Sans", sans-serif; font-weight: 600;
    color: var(--sun-orange); line-height: 1;
  }
  .card--contact .practice-name { left: 22px; top: 42px; }
  .practice-name__mark {
    display: block; width: 14px; height: 14px; border-radius: 50%;
    background: var(--sun-orange);
  }
  .card--contact .practice-name__mark { position: absolute; left: 0; top: -22px; }
  .practice-name__primary { display: block; font-size: 25px; letter-spacing: .5px; }
  .practice-name__secondary { display: block; font-size: 12.5px; margin-top: 3px; letter-spacing: .3px; }

  .doctors {
    position: absolute; right: 23px; top: 47px;
    font-family: "Raleway", sans-serif; font-weight: 500;
    font-size: 17.5px; line-height: 22px; text-align: right;
    color: var(--sun-orange);
  }
  .contact-band {
    position: absolute; left: 0; top: 111px; width: 100%; height: 102px;
    background: var(--band-yellow);
  }
  .contact-list {
    position: absolute; right: 23px; top: 21px; list-style: none;
    font-family: "Lato", sans-serif; font-size: 12.5px; line-height: 16px;
    color: var(--white); text-align: right;
  }
  .contact-list li { display: flex; justify-content: flex-end; align-items: center; gap: 4px; }
  .contact-list svg { width: 10px; height: 10px; flex: none; }
  .address {
    position: absolute; right: 24px; top: 231px;
    font-family: "Lato", sans-serif; font-size: 12.5px; color: var(--ink);
    word-spacing: 1px;
  }

  /* Brand side */
  .card--brand {
    left: 608px;
    background:
      linear-gradient(135deg, var(--magenta) 0%, #ef7a5a 22%, var(--band-yellow) 48%, #f3a430 66%, #ea6a63 86%, var(--magenta) 100%);
  }
  .card--brand .practice-name {
    left: 0; right: 0; top: 80px; text-align: center; color: var(--white);
  }
  .card--brand .practice-name__mark {
    width: 34px; height: 34px; margin: 0 auto 18px; background: var(--white);
  }
  .card--brand .practice-name__primary { font-size: 46px; letter-spacing: 1px; }
  .card--brand .practice-name__secondary { font-size: 22px; margin-top: 6px; letter-spacing: 1px; }
</style>
</head>
<body>
<main class="canvas">
  <section class="card card--contact" aria-label="Business card, contact side">
    <div class="practice-name">
      <span class="practice-name__mark"></span>
      <span class="practice-name__primary">maplebrook</span>
      <span class="practice-name__secondary">pediatric dentistry</span>
    </div>
    <p class="doctors">Mei-Ran Tsai, DMD<br>Corinne Walbeck, DMD</p>
    <div class="contact-band">
      <ul class="contact-list">
        <li>717.555.0193
          <svg viewBox="0 0 10 10" aria-hidden="true"><path fill="#fff" d="M2 1.5c.6-.5 1.2-.4 1.5.2l.6 1.2c.2.4 0 .8-.3 1l-.5.3c.4.9 1.1 1.6 2 2l.3-.5c.2-.3.6-.5 1-.3l1.2.6c.6.3.7.9.2 1.5-.7.8-1.8.8-3 .1C3.6 6.6 2.4 5.4 1.8 4 1.2 3 1.3 2.1 2 1.5z"/></svg></li>
        <li>Mei-ran@maplebrookkidsdental.example
          <svg viewBox="0 0 10 10" aria-hidden="true"><rect x="1" y="2" width="8" height="6" fill="#fff"/><path d="M1.3 2.4 5 5.3l3.7-2.9" fill="none" stroke="#f8b827" stroke-width=".8"/></svg></li>
        <li>Corinne@maplebrookkidsdental.example
          <svg viewBox="0 0 10 10" aria-hidden="true"><rect x="1" y="2" width="8" height="6" fill="#fff"/><path d="M1.3 2.4 5 5.3l3.7-2.9" fill="none" stroke="#f8b827" stroke-width=".8"/></svg></li>
        <li>www.maplebrookkidsdental.example
          <svg viewBox="0 0 10 10" aria-hidden="true"><circle cx="5" cy="5" r="4.2" fill="#fff"/><path d="M1 5h8M5 1c-2 2.4-2 5.6 0 8M5 1c2 2.4 2 5.6 0 8" fill="none" stroke="#f8b827" stroke-width=".7"/></svg></li>
      </ul>
    </div>
    <p class="address">482 Quarry Lane&nbsp; Suite 517&nbsp; Fairhollow, PA 17599</p>
  </section>

  <section class="card card--brand" aria-label="Business card, brand side">
    <div class="practice-name">
      <span class="practice-name__mark"></span>
      <span class="practice-name__primary">maplebrook</span>
      <span class="practice-name__secondary">pediatric dentistry</span>
    </div>
  </section>
</main>
</body>
</html>
```